Video Learning Web Application Site Design

We are a new company that produce and distribute educational videos using a subscription model on our website. The videos are streamed on our website and users can tailor their own course packages by creating playlists. Each video-lesson are also split into several smaller segments, and it should be easy to find and play those segments.

Please note that both the screenshots and wireframes provided are only how it looks right now, if you as the designer have a better idea on how to present it then please share it.
Updates

Please view the screenshots as well, I believe I forgot to include two buttons on the wireframes that should be on the Our Courses page. Also, there is no need to make a carbon copy of the wireframes/screenshots, I'd like you designers to come up with a better way of displaying the information if possible. For inspiration you can look at sites like ClipHarbor (I like the simplicity of their design) and to some extent the Tessel UI where they divide different areas of the page into clear "zones".

Thanks,

Project Deadline Extended
Reason: I have to extend the deadline because I've been really ill the last week. Will go through the current submissions now and provide feedback and looking forward to more submissions.

Target Market(s)

College and University students. Professionals wanting to expand their knowledge and people that want to learn new skills to get a promotion/new job.

Industry/Entity Type

Tailor

Requirements
Must have
• Must include the logo from the file "brainlark-logo".
• Should include two pages, one of the video-player page and one of the course list.
• Try to incorporate the colors from the logo.
• Please note: If you look at the video-player.png file just below "Åpne Tabell, lage..." there are two rows, those are sub-parts of the lesson. Both these and the main lesson itself must have some easy way to Play and Add to Playlist.
Nice to have
• We prefer flat design, with simple and clean icons. Don't overdo the colors, stay within 3-4 colors with variations of them.
Should not have
• 3D-like elements, lot of shadows or hard to ready text.

```html
<!DOCTYPE html>
<html lang="en">
<head>
<meta charset="utf-8">
<title>brainlark – Your Courses</title>
<link href="https://fonts.googleapis.com/css2?family=Source+Sans+3:wght@400;600;700&display=swap" rel="stylesheet">
<style>
  :root {
    --brand-blue: #1a7fa8;
    --navy: #003d5b;
    --navy-button: #0d4a66;
    --sky: #1ea4dd;
    --sky-link: #29a8e0;
    --orange: #e8841d;
    --orange-dark: #d06f10;
    --heading: #1a4a66;
    --text: #333333;
    --muted: #666666;
    --rule: #cfcfcf;
    --panel-band: #ebebeb;
    --footer-grey: #7a7a7a;
    --white: #ffffff;
  }
  * { box-sizing: border-box; margin: 0; padding: 0; }
  html, body { width: 1200px; height: 900px; overflow: hidden; background: var(--white); }
  body { position: relative; font-family: "Source Sans 3", "Helvetica Neue", Arial, sans-serif; color: var(--text); }
  .abs { position: absolute; }

  /* Header */
  .site-header { position: absolute; left: 0; top: 0; width: 1200px; height: 110px; background: var(--white); border-bottom: 2px solid #d9d9d9; }
  .brand { position: absolute; left: 122px; top: 24px; display: flex; align-items: center; gap: 14px; }
  .brand-dot { width: 58px; height: 58px; border-radius: 50%; background: var(--brand-blue); }
  .brand-name { font-size: 52px; font-weight: 700; color: var(--brand-blue); line-height: 1; letter-spacing: -0.5px; }
  .search { position: absolute; left: 450px; top: 35px; width: 310px; height: 36px; border: 2px solid #d4d4d4; border-radius: 18px; background: var(--white); overflow: hidden; }
  .search-button { position: absolute; right: 0; top: 0; width: 42px; height: 100%; background: var(--navy-button); display: flex; align-items: center; justify-content: center; }
  .session { position: absolute; right: 207px; top: 46px; font-size: 13px; font-weight: 600; color: var(--muted); }
  .btn-orange { background: var(--orange); color: var(--white); border: 1px solid var(--orange-dark); border-radius: 16px; font-weight: 600; display: flex; align-items: center; justify-content: center; }
  .logout { position: absolute; left: 1007px; top: 38px; width: 73px; height: 32px; font-size: 13px; }

  /* Sidebar */
  .sidebar { position: absolute; left: 0; top: 110px; width: 350px; height: 736px; background: var(--navy); }
  .nav-item { position: absolute; left: 126px; width: 212px; font-size: 14px; font-weight: 600; color: var(--white); display: flex; justify-content: space-between; align-items: center; }
  .nav-rule { position: absolute; left: 120px; width: 230px; height: 1px; background: #2a6381; }
  .nav-sub { position: absolute; left: 140px; font-size: 12px; font-weight: 600; color: var(--sky-link); }

  /* Main */
  .page-title { position: absolute; left: 370px; top: 125px; font-size: 18px; font-weight: 600; color: var(--sky); }
  .rule { position: absolute; left: 370px; width: 710px; height: 1px; background: var(--rule); }
  .player { position: absolute; left: 370px; top: 175px; width: 378px; height: 218px; background: linear-gradient(180deg, #f7f8f6 0%, #eef1ee 60%, #dfe6ea 100%); border: 1px solid #dcdcdc; }
  .play-big { position: absolute; left: 148px; top: 58px; width: 84px; height: 84px; border-radius: 50%; background: #aab8d8; border: 2px solid #dfe5f1; display: flex; align-items: center; justify-content: center; }
  .controls { position: absolute; left: 0; bottom: 0; width: 100%; height: 22px; background: #a9c4da; }
  .cue-panel { position: absolute; left: 769px; top: 175px; width: 310px; height: 219px; border: 1px solid #dedede; }
  .cue-title { position: absolute; left: 11px; top: 7px; font-size: 13px; font-weight: 700; color: var(--heading); }
  .cue-band { position: absolute; left: 0; top: 30px; width: 100%; height: 28px; background: var(--panel-band); }
  .cue-head { position: absolute; top: 35px; font-size: 13px; color: var(--orange); }
  .cue-divider { position: absolute; left: 121px; top: 30px; width: 1px; height: 188px; background: #dedede; }
  .cue-row { position: absolute; font-size: 11.5px; color: var(--text); }
  .course-name { position: absolute; left: 370px; top: 425px; font-size: 13px; font-weight: 700; color: var(--heading); }
  .remove { position: absolute; left: 530px; top: 420px; width: 160px; height: 28px; font-size: 13px; }
  .show-cues { position: absolute; left: 369px; top: 472px; width: 120px; height: 28px; border-radius: 14px; background: var(--navy-button); color: var(--white); font-size: 13px; font-weight: 700; display: flex; align-items: center; justify-content: center; border: 1px solid #06324a; }
  .tree-row { position: absolute; display: flex; align-items: center; }
  .tree-row svg { flex: none; }
  .tree-row.item { left: 363px; font-size: 13px; }
  .tree-row.child { left: 385px; font-size: 11.5px; }
  .tree-row .label { margin-left: 6px; color: var(--text); }

  /* Footer */
  .site-footer { position: absolute; left: 0; top: 846px; width: 1200px; height: 54px; border-top: 1px solid #d0d0d0; background: var(--white); }
  .footer-brand { position: absolute; left: 122px; top: 8px; display: flex; align-items: center; gap: 10px; }
  .footer-dot { width: 36px; height: 36px; border-radius: 50%; background: var(--footer-grey); }
  .footer-name { font-size: 33px; font-weight: 600; color: var(--footer-grey); line-height: 1; }
  .copyright { position: absolute; right: 120px; top: 17px; font-size: 12px; font-weight: 600; color: var(--muted); }
  .page-code { position: absolute; left: 1162px; top: 20px; font-size: 12px; font-weight: 700; color: var(--text); }
</style>
</head>
<body>
<svg width="0" height="0" style="position:absolute">
  <defs>
    <symbol id="icon-arrow" viewBox="0 0 12 12"><path d="M1 0 L12 6 L1 12 Z" fill="#0d4a66"/></symbol>
    <symbol id="icon-star" viewBox="0 0 24 24"><path d="M12 1.5 L15.1 8.4 L22.5 9.1 L16.9 14.1 L18.5 21.5 L12 17.7 L5.5 21.5 L7.1 14.1 L1.5 9.1 L8.9 8.4 Z" fill="#e8841d"/></symbol>
    <symbol id="icon-plus" viewBox="0 0 14 14"><circle cx="7" cy="7" r="7" fill="#fff"/><path d="M7 3.5v7M3.5 7h7" stroke="#003d5b" stroke-width="2"/></symbol>
    <symbol id="icon-minus" viewBox="0 0 14 14"><circle cx="7" cy="7" r="7" fill="#fff"/><path d="M3.5 7h7" stroke="#003d5b" stroke-width="2"/></symbol>
  </defs>
</svg>

<header class="site-header">
  <div class="brand"><span class="brand-dot"></span><span class="brand-name">brainlark</span></div>
  <div class="search">
    <div class="search-button">
      <svg width="16" height="16" viewBox="0 0 16 16"><circle cx="9.5" cy="6.5" r="4" fill="none" stroke="#fff" stroke-width="1.8"/><path d="M6.5 9.5 L2 14" stroke="#fff" stroke-width="2.2" stroke-linecap="round"/></svg>
    </div>
  </div>
  <div class="session">Logged in as mara@brainlark.net</div>
  <div class="btn-orange logout">LOGOUT</div>
</header>

<nav class="sidebar">
  <div class="nav-item" style="top:18px">INTRODUCTION <svg width="14" height="14"><use href="#icon-plus"/></svg></div>
  <div class="nav-rule" style="top:41px"></div>
  <div class="nav-item" style="top:47px">MODULES <svg width="14" height="14"><use href="#icon-minus"/></svg></div>
  <div class="nav-sub" style="top:77px">OUR COURSES</div>
  <div class="nav-sub" style="top:106px">YOUR COURSES</div>
  <div class="nav-rule" style="top:131px"></div>
  <div class="nav-item" style="top:139px">PLAYLISTS <svg width="14" height="14"><use href="#icon-plus"/></svg></div>
</nav>

<main>
  <h1 class="page-title">YOUR COURSES</h1>
  <div class="rule" style="top:157px"></div>

  <div class="player">
    <div class="abs" role="img" aria-label="Lesson video preview: spreadsheet with expense trends bar chart" style="left:0;top:0;width:100%;height:196px;"></div>
    <div class="play-big"><svg width="34" height="38" viewBox="0 0 34 38"><path d="M2 1 L33 19 L2 37 Z" fill="#fff"/></svg></div>
    <div class="controls">
      <svg width="378" height="22" viewBox="0 0 378 22">
        <circle cx="14" cy="11" r="8" fill="#4f6f9a"/>
        <path d="M11.5 7 L18 11 L11.5 15 Z" fill="#fff"/>
        <rect x="28" y="7" width="232" height="7" rx="3.5" fill="#6f8aa6"/>
        <circle cx="31" cy="10.5" r="3.5" fill="#e6eef5"/>
        <rect x="264" y="5" width="50" height="11" rx="2" fill="#7d97b7"/>
        <path d="M318 10.5 L324 7 L324 14 Z" fill="#e6eef5"/>
        <rect x="327" y="7" width="28" height="7" rx="3.5" fill="#e6eef5"/>
        <rect x="361" y="4" width="12" height="12" fill="#7d97b7"/>
      </svg>
    </div>
  </div>

  <section class="cue-panel">
    <div class="cue-title">ITEAM 1</div>
    <div class="cue-band"></div>
    <div class="cue-head" style="left:11px">Cues</div>
    <div class="cue-head" style="left:140px">Files</div>
    <div class="cue-divider"></div>
    <div class="cue-row" style="left:12px;top:69px">Child 1</div>
    <div class="cue-row" style="left:12px;top:98px">Child 2</div>
    <div class="cue-row" style="left:12px;top:127px">Child 3</div>
    <div class="cue-row" style="left:12px;top:156px">Child 4</div>
    <div class="cue-row" style="left:142px;top:69px">Download Leson file (xls)</div>
    <div class="cue-row" style="left:142px;top:98px">Download Study Material (doc)</div>
  </section>

  <div class="rule" style="top:413px"></div>
  <div class="course-name">Tabell 2013 - Beginner</div>
  <div class="btn-orange remove">Remove This Course</div>
  <div class="rule" style="top:455px"></div>

  <div class="show-cues">Show All Cues</div>

  <div class="tree-row item" style="top:515px"><svg width="12" height="12"><use href="#icon-arrow"/></svg><svg width="17" height="17" style="margin-left:7px"><use href="#icon-star"/></svg><span class="label">Item1</span></div>
  <div class="tree-row child" style="top:543px"><svg width="12" height="12"><use href="#icon-arrow"/></svg><svg width="17" height="17" style="margin-left:7px"><use href="#icon-star"/></svg><span class="label">Child 1</span></div>
  <div class="tree-row child" style="top:574px"><svg width="12" height="12"><use href="#icon-arrow"/></svg><svg width="17" height="17" style="margin-left:7px"><use href="#icon-star"/></svg><span class="label">Child 2</span></div>
  <div class="tree-row child" style="top:605px"><svg width="12" height="12"><use href="#icon-arrow"/></svg><svg width="17" height="17" style="margin-left:7px"><use href="#icon-star"/></svg><span class="label">Child 3</span></div>
  <div class="tree-row child" style="top:635px"><svg width="12" height="12"><use href="#icon-arrow"/></svg><svg width="17" height="17" style="margin-left:7px"><use href="#icon-star"/></svg><span class="label">Child 4</span></div>
  <div class="tree-row item" style="top:664px"><svg width="12" height="12"><use href="#icon-arrow"/></svg><svg width="17" height="17" style="margin-left:7px"><use href="#icon-star"/></svg><span class="label">Item2</span></div>
  <div class="tree-row child" style="top:692px"><svg width="12" height="12"><use href="#icon-arrow"/></svg><svg width="17" height="17" style="margin-left:7px"><use href="#icon-star"/></svg><span class="label">Child 5</span></div>
  <div class="tree-row child" style="top:723px"><svg width="12" height="12"><use href="#icon-arrow"/></svg><svg width="17" height="17" style="margin-left:7px"><use href="#icon-star"/></svg><span class="label">Child 6</span></div>
  <div class="tree-row child" style="top:754px"><svg width="12" height="12"><use href="#icon-arrow"/></svg><svg width="17" height="17" style="margin-left:7px"><use href="#icon-star"/></svg><span class="label">Child 7</span></div>
  <div class="tree-row item" style="top:788px"><svg width="12" height="12"><use href="#icon-arrow"/></svg><svg width="17" height="17" style="margin-left:7px"><use href="#icon-star"/></svg><span class="label">Item3</span></div>
  <div class="tree-row child" style="top:816px"><svg width="12" height="12"><use href="#icon-arrow"/></svg><svg width="17" height="17" style="margin-left:7px"><use href="#icon-star"/></svg><span class="label">Child 8</span></div>
</main>

<footer class="site-footer">
  <div class="footer-brand"><span class="footer-dot"></span><span class="footer-name">brainlark</span></div>
  <div class="copyright">© 2013 brainlark | All Rights Reserved.</div>
  <div class="page-code">C2</div>
</footer>
</body>
</html>
```